TK Homes - Stone Dorf Design

Looking for a double sides design, 1 side for my realestate and the other for home building. ( TK Homes on 1 side, Stone Dorf card on the other Side
Side 1 - Marek Tove ~ Vox Realty logo and Company ( the Property quarter )
Marek Tove
Marek@Marektove.example
IG - Marek_Bzq_Realtor
FB - marekt
Cell - 5558130467
3847 61 St Nw

Side 2
Marek Tove
5558130467
IG - Stonedorf_Bzq
Stonedorfdev@mailbox.example

Target Market(s)

Home buyers/ sellers

Industry/Entity Type

Home builders - Realestate

Contact Information for Business Card

Above

Requirements
Must have
• Black OR White background - my information -

```html
<!DOCTYPE html>
<html lang="en">
<head>
<meta charset="utf-8">
<title>Marek Tove – Business Cards</title>
<link rel="stylesheet" href="https://fonts.googleapis.com/css2?family=Tinos:wght@400;700&display=swap">
<style>
  :root {
    --stage: #232325;
    --card: #212126;
    --blue: #0a72bd;
    --yellow: #fdcb40;
    --white: #ffffff;
  }
  * { margin: 0; padding: 0; box-sizing: border-box; }
  html, body {
    width: 1200px; height: 780px; overflow: hidden;
    background: var(--stage);
    font-family: "Tinos", "Times New Roman", serif;
  }
  .stage {
    width: 1200px; height: 780px;
    display: flex; align-items: center; justify-content: center; gap: 40px;
  }
  .card {
    position: relative;
    width: 560px; height: 320px;
    background: var(--card);
    border-radius: 18px;
    overflow: hidden;
    box-shadow: 0 18px 40px rgba(0,0,0,0.55);
  }
  .card-art { position: absolute; inset: 0; width: 100%; height: 100%; }
  .brand {
    position: absolute; left: 0; width: 250px; text-align: center;
    color: var(--blue); font-weight: 700;
  }
  .brand-homes { top: 128px; font-size: 36px; }
  .brand-personal { top: 122px; font-size: 38px; }
  .brand-mark {
    display: block; width: 14px; height: 14px; margin: 0 auto 10px;
    background: var(--yellow);
  }
  .details { position: absolute; left: 292px; top: 62px; }
  .name { font-size: 30px; font-weight: 700; line-height: 1; }
  .name .first { color: var(--blue); }
  .name .last { color: var(--yellow); }
  .title { color: var(--white); font-size: 15px; font-weight: 700; margin-top: 4px; }
  .contacts { list-style: none; margin-top: 14px; }
  .contacts li {
    display: flex; align-items: center; gap: 8px;
    color: var(--white); font-size: 14px; line-height: 21px;
  }
  .contacts svg { width: 13px; height: 13px; flex: none; }
  .address {
    position: absolute; left: 292px; top: 248px;
    color: var(--white); font-size: 15px;
  }
</style>
</head>
<body>
<main class="stage">

  <section class="card card-homes">
    <svg class="card-art" viewBox="0 0 560 320" aria-hidden="true">
      <line x1="225" y1="60" x2="262" y2="210" stroke="#ffffff" stroke-width="1"/>
      <polygon points="0,298 335,298 318,320 0,320" fill="var(--yellow)"/>
      <polygon points="318,282 560,282 560,320 325,320 345,296 310,296" fill="var(--card)"/>
      <polygon points="326,284 560,284 560,320 338,320 355,294 320,294" fill="var(--blue)"/>
    </svg>
    <div class="brand brand-homes"><span class="brand-mark"></span>Stone Dorf</div>
    <div class="details">
      <div class="name"><span class="first">Marek</span> <span class="last">Tove</span></div>
      <div class="title">Director</div>
      <ul class="contacts">
        <li><svg viewBox="0 0 16 16"><path d="M4 1l3 3-2 2c1 2 3 4 5 5l2-2 3 3-2 3C7 15 1 9 1 3z" fill="var(--blue)"/></svg>5558130467</li>
        <li><svg viewBox="0 0 16 16"><circle cx="8" cy="8" r="7" fill="var(--blue)"/></svg>Stonedorf_Bzq</li>
        <li><svg viewBox="0 0 16 16"><rect x="1" y="3" width="14" height="10" fill="var(--blue)"/><path d="M1 3l7 6 7-6" stroke="var(--card)" fill="none"/></svg>Stonedorfdev@mailbox.example</li>
      </ul>
    </div>
  </section>

  <section class="card card-personal">
    <svg class="card-art" viewBox="0 0 560 320" aria-hidden="true">
      <line x1="225" y1="60" x2="262" y2="210" stroke="#ffffff" stroke-width="1"/>
      <polygon points="0,298 335,298 318,320 0,320" fill="var(--yellow)"/>
      <polygon points="326,284 560,284 560,320 338,320 355,294 320,294" fill="var(--blue)"/>
    </svg>
    <div class="brand brand-personal"><span class="brand-mark"></span>Marek Tove</div>
    <div class="details">
      <div class="name"><span class="first">Marek</span> <span class="last">Tove</span></div>
      <div class="title">Director</div>
      <ul class="contacts">
        <li><svg viewBox="0 0 16 16"><path d="M4 1l3 3-2 2c1 2 3 4 5 5l2-2 3 3-2 3C7 15 1 9 1 3z" fill="var(--blue)"/></svg>5558130467</li>
        <li><svg viewBox="0 0 16 16"><circle cx="8" cy="8" r="7" fill="var(--blue)"/></svg>marekt</li>
        <li><svg viewBox="0 0 16 16"><circle cx="8" cy="8" r="7" fill="var(--blue)"/></svg>Marek_Bzq_Realtor</li>
        <li><svg viewBox="0 0 16 16"><rect x="1" y="3" width="14" height="10" fill="var(--blue)"/><path d="M1 3l7 6 7-6" stroke="var(--card)" fill="none"/></svg>Marek@Marektove.example</li>
        <li><svg viewBox="0 0 16 16"><circle cx="8" cy="8" r="6.5" fill="none" stroke="var(--blue)" stroke-width="1.5"/><ellipse cx="8" cy="8" rx="3" ry="6.5" fill="none" stroke="var(--blue)"/><line x1="1.5" y1="8" x2="14.5" y2="8" stroke="var(--blue)"/></svg>www.marektove.example</li>
      </ul>
    </div>
    <div class="address">3847 61 St Nw</div>
  </section>

</main>
</body>
</html>
```